Banner für Immobilienmakler
Zielgruppe
Immobilienmakler, Immobilienverkauf mit Herz,
Aufgabenstellung
Verkauf von Häusern und Wohnungen, der Banner soll an einen Balkon oder einen Zaun angebracht werden mit dem Hinweis, dass das Haus Zu verkaufen ist.
Maße ca. 76 x 244cm
Es darf gerne frech und modern sein mit einem witzigen einladenden Spruch sein, sollte aber auch ansonsten zu meinem chicen Style passen (siehe Homepage www.karwendimmobilien.de) es soll sich abheben von anderen langweiligen Bannern.
Ggf soll die Plane auch noch an einem Tennisplatz angebracht werden

```html
<!DOCTYPE html>
<html lang="de">
<head>
<meta charset="utf-8">
<title>Banner – Karwend Immobilien</title>
<link rel="stylesheet" href="https://fonts.googleapis.com/css2?family=Archivo:wdth,wght@62..125,100..900&display=swap">
<style>
  :root {
    --page-bg: #e6e6e6;
    --ink: #262626;
    --band: #2c2c2c;
    --gold: #cfa95f;
    --cream: #efe6d2;
    --white: #ffffff;
  }
  * { margin: 0; padding: 0; box-sizing: border-box; }
  html, body {
    width: 1200px; height: 720px; overflow: hidden;
    background: var(--page-bg);
    font-family: "Archivo", Arial, sans-serif;
  }
  .banner {
    position: absolute; left: 30px; top: 173px;
    width: 1140px; height: 375px;
    overflow: hidden;
    box-shadow: 0 14px 24px rgba(0,0,0,0.12);
  }
  .banner__art { position: absolute; inset: 0; }
  .headline {
    position: absolute; color: var(--ink); white-space: nowrap;
  }
  .headline--intro {
    left: 480px; top: 52px;
    font-size: 60px; font-weight: 400; letter-spacing: -0.5px;
  }
  .headline--main {
    left: 532px; top: 122px;
    font-size: 58px; font-weight: 800; letter-spacing: -1px;
    font-stretch: 90%;
  }
  .sale-strip-text {
    position: absolute; left: 386px; top: 192px;
    font-size: 36px; font-weight: 500; color: var(--white);
    white-space: nowrap; letter-spacing: -0.3px;
    font-stretch: 95%;
  }
  .sale-strip-text strong { color: var(--gold); font-weight: 700; }
  .contact {
    position: absolute; top: 296px; height: 79px;
    display: flex; align-items: center; gap: 10px;
    color: var(--white); white-space: nowrap;
  }
  .contact svg { flex: none; }
  .contact--phone { left: 34px; font-size: 30px; font-weight: 700; }
  .contact--mail { left: 370px; font-size: 20px; font-weight: 500; }
  .contact--web { left: 704px; font-size: 20px; font-weight: 500; }
  .brand-seal {
    position: absolute; left: 1016px; top: 256px;
    width: 94px; height: 94px; border-radius: 50%;
    background: var(--band);
    border: 2px solid var(--cream);
    display: flex; align-items: center; justify-content: center;
    text-align: center;
    color: var(--white); font-size: 10px; font-weight: 500;
    line-height: 1.3; letter-spacing: 0.5px;
  }
</style>
</head>
<body>
  <div class="banner">
    <svg class="banner__art" width="1140" height="375" viewBox="0 0 1140 375">
      <defs>
        <linearGradient id="photoTones" x1="0" y1="0" x2="1" y2="1">
          <stop offset="0" stop-color="#d9d4cc"/>
          <stop offset="0.5" stop-color="#c9b59a"/>
          <stop offset="1" stop-color="#a9835b"/>
        </linearGradient>
        <linearGradient id="woodTones" x1="0" y1="0" x2="1" y2="1">
          <stop offset="0" stop-color="#e9dcc0"/>
          <stop offset="0.5" stop-color="#f1e8d6"/>
          <stop offset="1" stop-color="#dcc697"/>
        </linearGradient>
      </defs>
      <rect class="wood-surface" x="0" y="0" width="1140" height="300" fill="url(#woodTones)" role="img" aria-label="Helle Holzmaserung mit goldenen Linien"/>
      <polygon class="family-photo" points="0,0 452,0 290,300 0,300" fill="url(#photoTones)" role="img" aria-label="Foto: Familie beim Umzug, Kind sitzt lachend in einem Umzugskarton"/>
      <polygon class="sale-strip" points="366,190 1110,188 1110,235 338,237" fill="var(--band)"/>
      <rect class="contact-band" x="0" y="296" width="1140" height="79" fill="var(--band)"/>
    </svg>

    <div class="headline headline--intro">Lust auf einen</div>
    <div class="headline headline--main">TAPETENWECHSEL?</div>
    <div class="sale-strip-text">DIESE IMMOBILIE STEHT <strong>ZUM VERKAUF!</strong></div>

    <div class="contact contact--phone">
      <svg width="26" height="26" viewBox="0 0 24 24"><path d="M6.6 2.5l3 3.5-1.8 2.6c1.2 2.8 3.4 5 6.2 6.2l2.6-1.8 3.5 3-1.7 3.4C10 18.6 5.4 14 3.2 4.2z" fill="var(--gold)"/></svg>
      02241 / 47 31 628
    </div>
    <div class="contact contact--mail">
      <svg width="26" height="18" viewBox="0 0 26 18"><rect x="0" y="0" width="26" height="18" fill="var(--gold)"/><path d="M0 0l13 10L26 0" fill="none" stroke="var(--band)" stroke-width="1.6"/></svg>
      info@karwendimmobilien.de
    </div>
    <div class="contact contact--web">
      <svg width="26" height="26" viewBox="0 0 26 26" fill="none" stroke="var(--gold)" stroke-width="1.8"><circle cx="13" cy="13" r="11.5"/><ellipse cx="13" cy="13" rx="5" ry="11.5"/><path d="M1.5 13h23M3.5 7h19M3.5 19h19"/></svg>
      www.karwendimmobilien.de
    </div>

    <div class="brand-seal">KARWEND<br>IMMOBILIEN</div>
  </div>
</body>
</html>
```